Telecommunications/Power civil contractor needs business card design

Were a new telecommunications/power underground civil contractor that is looking for a new business card design. Our company colours are silver or grey and orange. Feel free to use the white background logo or the black background logo.

Target Market(s)

Local contractors, utility companies, private sector mining/energy companies, developers.

Industry/Entity Type

Telecommunications

Contact Information for Business Card

Each card will need the following info:
Persons name:
Title:
E-mail:
Phone number:
Shop Address:
Mailing Address:

Requirements
Must have
• Each card will need the following info:
• Persons name:
• Title:
• E-mail:
• Phone number:
• Shop Address:
• Mailing Address:

```html
<!DOCTYPE html>
<html lang="en">
<head>
<meta charset="utf-8">
<title>Northline Civil Works Inc – Business Card</title>
<link rel="stylesheet" href="https://fonts.googleapis.com/css2?family=Open+Sans:wght@400;600;700&display=swap">
<style>
  :root {
    --page-bg: #e6e2dc;
    --card-bg: #f6f6f4;
    --accent: #d8462a;
    --accent-band: #d4523a;
    --ink: #3b3b3b;
    --ink-soft: #555555;
    --mark-grey: #8a8a8a;
  }
  * { margin: 0; padding: 0; box-sizing: border-box; }
  html, body {
    width: 1200px;
    height: 969px;
    overflow: hidden;
    background: var(--page-bg);
    font-family: "Open Sans", Arial, sans-serif;
  }
  .card {
    position: absolute;
    left: 100px;
    top: 202px;
    width: 1000px;
    height: 564px;
    background: var(--card-bg);
    box-shadow: 0 10px 30px rgba(0, 0, 0, 0.12);
  }
  .card__band {
    position: absolute;
    left: 26px;
    top: 0;
    width: 39px;
    height: 100%;
    background: var(--accent-band);
  }
  .person {
    position: absolute;
    left: 112px;
    top: 232px;
  }
  .person__name {
    font-size: 34px;
    font-weight: 600;
    color: var(--accent);
    letter-spacing: 0.5px;
    line-height: 1.2;
  }
  .person__title {
    font-size: 25px;
    font-weight: 400;
    color: var(--ink-soft);
    line-height: 1.3;
  }
  .brand {
    position: absolute;
    right: 54px;
    top: 56px;
    display: flex;
    flex-direction: column;
    align-items: flex-end;
  }
  .brand__mark {
    width: 150px;
    height: 150px;
    margin-right: 70px;
  }
  .brand__name {
    margin-top: 22px;
    font-size: 30px;
    font-weight: 700;
    color: var(--accent);
    text-align: right;
    line-height: 1.15;
    letter-spacing: 1px;
  }
  .contact {
    position: absolute;
    right: 54px;
    bottom: 36px;
    text-align: right;
    color: var(--ink);
    font-size: 25px;
    font-weight: 400;
    line-height: 1.6;
  }
</style>
</head>
<body>
  <div class="card">
    <div class="card__band"></div>

    <div class="person">
      <p class="person__name">DANA MORROW</p>
      <p class="person__title">CEO/Founder</p>
    </div>

    <div class="brand">
      <svg class="brand__mark" viewBox="0 0 150 150" aria-hidden="true">
        <circle cx="75" cy="75" r="70" fill="none" stroke="var(--mark-grey)" stroke-width="6"/>
      </svg>
      <p class="brand__name">NORTHLINE<br>CIVIL WORKS INC</p>
    </div>

    <div class="contact">
      <p class="contact__shop">Shop: 4120 Birchwood Road, Fairbanks, Alaska 99701</p>
      <p class="contact__mailing">Mailing: PO Box 8812, Fairbanks, Alaska 99708</p>
      <p class="contact__lines">555 214 7390 | dana@northlinecivil.com | www.northlinecivil.com</p>
    </div>
  </div>
</body>
</html>
```